Forex website redesign

We need an attractive good looking website design that increase the apatite of our visitors to subscribe to our advisory service, beside the fact that we do offer very high quality service.

Our service is where we connect to investor accounts who are subscribed, to automatically deliver and execute our advise to buy or sell straight onto their account using high tech software.

The final design should communicate financial safty and growth.
Updates

Here is something to keep in mind about our business model that may help you in your design, we SHOW people the right way to invest, so they can make money instead of going somewere else and lose it. Beside that point, most websites in forex that includes pictures of happy and excited people who make money ALWAY turn out to be scam. So please try not to position our business that way in visitor first impression once he/she visit our site.

Thank you for your help :)

Target Market(s)

Financial Market, 20-70 years old

Industry/Entity Type

Financial

Requirements
Must have
• Call to action feature + Logo redesign. Please visit www.veldoramarkets.com to get an idea of how we want it. Also include the personal photos of our advisors in your deign.

```html
<!DOCTYPE html>
<html lang="en">
<head>
<meta charset="utf-8">
<title>Veldora FX</title>
<link href="https://fonts.googleapis.com/css2?family=Roboto:wght@400;500;700&family=Roboto+Condensed:wght@300;400;700&display=swap" rel="stylesheet">
<style>
:root{
  --green:#4cb81a;
  --navy:#1a4a7a;
  --grey-icon:#b3b3b3;
  --text:#333333;
  --muted:#555555;
  --rule:#dddddd;
  --orange:#f7931e;
  --btn-blue:#b7c9db;
  --quote-bg:#e5e7df;
}
*{margin:0;padding:0;box-sizing:border-box}
html,body{width:800px;height:1200px;overflow:hidden;background:#fff}
body{position:relative;font-family:"Roboto",Arial,sans-serif;color:var(--text)}
.abs{position:absolute}
.brand{font-weight:700;color:var(--green);font-size:24px;letter-spacing:.2px}
.brand-mark{display:inline-block;width:14px;height:14px;background:var(--navy);margin-right:8px;vertical-align:middle}
.tagline{font-size:11.5px;color:#666}
.tagline b{color:#555}
.nav{left:67px;top:106px;width:666px;border-top:1px solid var(--rule);display:flex;justify-content:space-around;font-size:10px;color:#555;padding-top:8px}
.nav span{padding:0 4px 8px}
.nav .active{border-bottom:2px solid var(--navy);color:#333}
.hero{left:67px;top:135px;width:666px;height:230px;background:linear-gradient(180deg,#1c6fd0 0%,#3aa3ef 45%,#1560c0 100%);overflow:hidden}
.hero-shadow{left:80px;top:365px;width:640px;height:20px;background:radial-gradient(ellipse at top,rgba(0,0,0,.45),rgba(0,0,0,0) 70%)}
.hero-kicker{left:0;width:666px;top:18px;text-align:center;color:#fff;font-weight:500;font-size:14px}
.hero-title{left:0;width:666px;top:56px;text-align:center;color:#fff;font-family:"Roboto Condensed",sans-serif;font-weight:700;font-size:44px;letter-spacing:-1px}
.hero-sub{left:0;width:666px;top:108px;text-align:center;color:#111;font-family:"Roboto Condensed",sans-serif;font-weight:300;font-size:44px;letter-spacing:-1.5px}
.dots{left:306px;top:208px;display:flex;gap:9px}
.dots i{width:12px;height:12px;border-radius:50%;background:#1b3e72;display:block}
.intro{left:70px;top:399px;width:660px;text-align:center;font-family:"Roboto Condensed",sans-serif;font-weight:300;font-size:13px;line-height:17px;letter-spacing:-.2px;color:#333}
.intro b{font-family:"Roboto",sans-serif;font-weight:700;font-size:13.5px;letter-spacing:0}
.live-btn{left:320px;top:440px;width:174px;height:29px;border-radius:6px;background:var(--btn-blue);color:#fff;font-size:10.5px;font-weight:500;text-align:center;line-height:29px}
.diamond{width:60px;height:60px;transform:rotate(45deg)}
.col-title{font-size:14px;font-weight:500;color:#444;text-align:center;width:200px}
.small{font-family:Arial,sans-serif;font-size:7.7px;line-height:9.6px;color:#444}
.photo{width:51px;height:55px;background:linear-gradient(135deg,#c9b9a8,#6b5a4f)}
.more{width:88px;height:18px;border:1px solid #cfcfcf;border-radius:9px;font-size:8px;line-height:16px;padding-left:10px;color:#222;box-shadow:0 1px 2px rgba(0,0,0,.12)}
.more::after{content:"····›";color:var(--green);position:absolute;right:10px;font-size:8px}
.pitch{font-family:"Roboto Condensed",sans-serif;font-weight:300;font-size:17px;letter-spacing:-.4px;color:#555;line-height:22px;white-space:nowrap}
.order-badge{width:46px;height:46px;border-radius:50%;background:var(--orange);color:#fff;font-family:"Roboto Condensed",sans-serif;font-weight:300;font-size:13px;line-height:14px;text-align:center;padding-top:9px}
.sec-title{font-size:14px;font-weight:500;color:#444}
.quote{left:89px;top:842px;width:420px;height:77px;background:var(--quote-bg);border-radius:5px;padding:16px 20px;font-family:Arial,sans-serif;font-size:8.6px;line-height:11px;color:#444}
.cta{left:102px;top:973px;font-family:"Roboto Condensed",sans-serif;font-weight:300;font-size:19px;color:#555}
.cta b{font-family:"Roboto",sans-serif;font-weight:700;color:var(--orange);font-size:18px;margin-left:16px}
.footer-rule{left:67px;top:1015px;width:666px;border-top:1px solid var(--rule)}
.foot-col h4{font-size:13.5px;font-weight:700;color:#444;margin-bottom:8px;letter-spacing:.3px}
.foot-col p{font-family:Arial,sans-serif;font-size:8px;color:#444;line-height:15.5px}
.foot-col .chat{color:var(--green);font-weight:700}
.social{display:flex;gap:5px}
.social i{width:18px;height:18px;border-radius:50%;background:var(--grey-icon);display:block}
</style>
</head>
<body>

<header>
  <div class="abs" style="left:300px;top:40px"><span class="brand-mark"></span><span class="brand">Veldora FX</span></div>
  <div class="abs tagline" style="left:300px;top:77px">From Traders to Traders, <b>THE REAL DEAL</b></div>
  <nav class="abs nav">
    <span class="active">Home</span><span>About Us</span><span>Order</span><span>Performance »</span><span>Lian Wei Special</span><span>Terms &amp; Conditions</span><span>Why Us?</span><span>Contact Us</span>
  </nav>
</header>

<section class="abs hero" role="img" aria-label="Blue trading backdrop with charts, laptops and a trader raising his arms">
  <div class="abs hero-kicker">The one stop shop for the best forex signals</div>
  <div class="abs hero-title">ACHIEVE</div>
  <div class="abs hero-sub">THE HIGHEST RESULTS</div>
  <div class="abs dots"><i></i><i></i><i></i><i></i></div>
</section>
<div class="abs hero-shadow"></div>

<p class="abs intro"><b>Veldora FX LTD</b> is the ONLY forex signal service on this planet that provides full info about the traders involved including<br>REAL personal photos, REAL personal details and portfolios, as well as YEARS of verified and consistent live trading performance.</p>
<div class="abs live-btn">Click here to See Live Results</div>

<div class="abs diamond" style="left:141px;top:500px;background:var(--green)"></div>
<svg class="abs" style="left:158px;top:518px" width="26" height="24" viewBox="0 0 26 24"><rect x="3" y="3" width="20" height="13" fill="none" stroke="#fff" stroke-width="2"/><path d="M13 16v4M8 21h10" stroke="#fff" stroke-width="2"/></svg>
<div class="abs diamond" style="left:363px;top:500px;background:var(--navy)"></div>
<svg class="abs" style="left:381px;top:518px" width="24" height="24" viewBox="0 0 24 24"><circle cx="12" cy="12" r="7" fill="none" stroke="var(--green)" stroke-width="3" stroke-dasharray="3 2"/><circle cx="12" cy="12" r="3" fill="var(--green)"/></svg>
<div class="abs diamond" style="left:596px;top:500px;background:var(--grey-icon)"></div>
<svg class="abs" style="left:615px;top:518px" width="22" height="22" viewBox="0 0 22 22"><rect x="2" y="9" width="4" height="10" fill="var(--navy)"/><path d="M8 9l5-7c2 0 2 2 1 5h5c1 0 2 1 1 2l-2 9H8z" fill="var(--navy)"/></svg>

<h3 class="abs col-title" style="left:71px;top:581px">About Us</h3>
<h3 class="abs col-title" style="left:293px;top:581px">How Signals Work</h3>
<h3 class="abs col-title" style="left:526px;top:581px">Order Now</h3>

<div class="abs photo" style="left:91px;top:613px" role="img" aria-label="Portrait photo of the lead advisor"></div>
<p class="abs small" style="left:152px;top:613px;width:126px">We are a group of investors who are mainly interested in Forex. Our non-stop search for Forex elite traders has began back in 2003, we have read and analyzed countless number of portfolios</p>
<p class="abs small" style="left:92px;top:677px;width:190px">and we have developed advance and superior analytic skills over time and have built up a wide connection with what we believe are the best Forex traders on this planet.</p>

<p class="abs small" style="left:318px;top:613px;width:188px">Once you subscribe, you will be re-directed to a secure page to download and set-up the EA copier on your VPS with all the instructions you need(We provide full support, and we can set it up for you for no additional charge.<br><br>Once set-up, the software is of superior quality and copies flawlessly, and you have direct and total control over your account. Whereas your subscription will be renewed automatically by the end of the cycle you choose (Monthly/OR/4 months).</p>

<p class="abs pitch" style="left:545px;top:610px">Let us do the picks,<br>while you enjoy the</p>
<div class="abs order-badge" style="left:672px;top:610px">Order<br>Now</div>
<p class="abs small" style="left:545px;top:663px;width:187px">Once set-up, the software is of superior quality and copies flawlessly, and you have direct and total control over your account. Whereas your subscription will be renewed automatically by the end of the cycle you choose (Monthly/OR/4 months).</p>

<div class="abs more" style="left:91px;top:740px">Read More</div>
<div class="abs more" style="left:317px;top:740px">Read More</div>
<div class="abs more" style="left:544px;top:740px">Read More</div>

<svg class="abs" style="left:92px;top:801px" width="30" height="22" viewBox="0 0 30 22"><ellipse cx="12" cy="13" rx="10" ry="6" fill="var(--green)"/><ellipse cx="18" cy="8" rx="10" ry="7" fill="var(--navy)"/></svg>
<h3 class="abs sec-title" style="left:127px;top:805px">Testimonials</h3>
<div class="abs quote">Loren text we have developed advance and superior analytic skills over time and have built up a wide connection with what we believe are the best Forex traders on this planet.<br><b>Marco Reid</b><br>USA</div>
<div class="abs more" style="left:91px;top:934px">Read More</div>

<svg class="abs" style="left:543px;top:803px" width="22" height="22" viewBox="0 0 22 22"><circle cx="11" cy="11" r="8.5" fill="none" stroke="var(--navy)" stroke-width="2.5"/><path d="M5 5l12 12" stroke="var(--navy)" stroke-width="2.5"/></svg>
<h3 class="abs sec-title" style="left:572px;top:806px">Risk Disclaimer</h3>
<p class="abs small" style="left:544px;top:845px;width:190px">Once set-up, the software is of superior quality and copies flawlessly, and you have direct and total control over your account. Whereas your subscription will be renewed automatically by the end of the cycle you choose (Monthly/OR/4 months).</p>
<div class="abs more" style="left:540px;top:928px">Read More</div>

<div class="abs cta">Let us do the picks, while you enjoy the <b>Order Now</b></div>

<footer>
  <div class="abs footer-rule"></div>
  <div class="abs foot-col" style="left:93px;top:1034px"><h4>ABOUT US</h4><p>COMPANY INFO<br>SERVICES<br>TEAM<br>SOLUTIONS</p></div>
  <div class="abs foot-col" style="left:216px;top:1034px"><h4>ADVICE</h4><p>FAQS<br>ACCOUNT<br>CONTACTS<br><span class="chat">Live Chat</span></p></div>
  <div class="abs foot-col" style="left:323px;top:1034px"><h4>JOIN IN</h4><p>SIGN UP<br>FORUMS<br>PROMOTIONS</p></div>
  <div class="abs foot-col" style="left:423px;top:1034px"><h4>FOLLOW US</h4><div class="social"><i></i><i></i><i></i><i></i></div></div>
  <div class="abs" style="left:545px;top:1044px"><span class="brand-mark"></span><span class="brand" style="font-size:17px">Veldora FX</span></div>
  <div class="abs tagline" style="left:578px;top:1067px;font-size:8px">From Traders to Traders, <b>THE REAL DEAL</b></div>
  <div class="abs" style="left:555px;top:1097px;font-family:Arial,sans-serif;font-size:8px;color:#444">© 2013 | PRIVACY POLICY</div>
</footer>

</body>
</html>
```